Re-style home page - eye-catching and unique design for social commerce website

We need a new concept design for BrinoKet's home page.
We don't want to make huge changes but creating a more professional and eye-catching style.

We need to look very serious like a professional services company and in the same time to look like a social network for e-commerce.

Our logo is very captive and you can use to creating something of harmonious.

This is a re-style and I'm excepted to see unique and fresh design like Glimmora.

Target Market(s)

e-commerce and social

Industry/Entity Type

Social

Number of Pages Required

1 page

Font styles to use
Serif
Sans Serif

Requirements
Must have
• An eye-catching result.
• Search bar with logo and Login How it works and business
• The slogan with login and signup.
• Footer links.
Nice to have
• I would like to open the home page and see only two clear ways:
• -Consumer
• --Search
• --The slogan
• --Login and Signup
• --How it works
• -Business
• --Go to Business area
• Background: City, Shopping.
Should not have
• Scrollbar style!

```html
<!DOCTYPE html>
<html lang="en">
<head>
<meta charset="utf-8">
<title>BrinoKet — Shop directly from your profile</title>
<link href="https://fonts.googleapis.com/css2?family=Open+Sans:wght@400;600;700&family=Raleway:wght@800&display=swap" rel="stylesheet">
<style>
:root{
  --bar:#262626;
  --white:#ffffff;
  --ink:#1b1b1b;
  --yellow:#f3cb22;
  --purple:#7e7ce6;
  --orange:#f2673a;
  --pink:#e5365d;
  --panel:rgba(40,38,36,.86);
  --btn-yellow:#f0e23a;
  --link-blue:#2b3fd8;
  --social:#6477b8;
}
*{box-sizing:border-box;margin:0;padding:0}
html,body{width:1200px;height:909px;overflow:hidden}
body{position:relative;font-family:"Open Sans",sans-serif;color:var(--ink);background:var(--bar)}
.hero-bg{position:absolute;left:0;top:91px;width:1200px;height:764px;
  background:
   radial-gradient(ellipse 120px 260px at 110px 480px,rgba(30,160,150,.55),transparent),
   radial-gradient(ellipse 110px 240px at 1110px 470px,rgba(200,40,90,.55),transparent),
   radial-gradient(ellipse 160px 200px at 230px 560px,rgba(220,60,120,.45),transparent),
   radial-gradient(ellipse 180px 220px at 1000px 560px,rgba(210,150,40,.45),transparent),
   linear-gradient(180deg,#cfc6b4 0%,#b9ad97 45%,#8d7a66 75%,#6b5846 100%)}
.topbar{position:absolute;left:0;top:0;width:1200px;height:91px;background:var(--bar)}
.brand{position:absolute;left:127px;top:20px;font-weight:700;font-size:40px;color:var(--white);line-height:46px;display:flex;align-items:center;gap:12px}
.brand-dot{width:30px;height:30px;border-radius:50%;background:var(--yellow)}
.search{position:absolute;left:436px;top:30px;width:333px;height:34px;display:flex;border-radius:3px;overflow:hidden}
.search-field{flex:1;background:#ececec;font-size:13px;color:#999;padding:0 14px;line-height:34px}
.search-btn{width:40px;background:var(--yellow);display:flex;align-items:center;justify-content:center}
.nav{position:absolute;left:786px;top:38px;color:var(--white);font-size:13.5px;display:flex;gap:12px}
.login-toggle{position:absolute;left:979px;top:30px;width:92px;height:34px;border:2px solid var(--white);border-radius:3px;color:var(--white);font-weight:600;font-size:16px;text-align:center;line-height:30px}
.login-panel{position:absolute;left:807px;top:83px;width:264px;height:172px;background:rgba(235,232,228,.92);border-radius:3px;padding:13px}
.login-panel::before{content:"";position:absolute;right:36px;top:-8px;border:8px solid transparent;border-top:0;border-bottom-color:rgba(235,232,228,.92)}
.input{height:33px;background:var(--white);border:1px solid #ddd;border-radius:3px;font-size:12.5px;color:#999;padding:0 10px;line-height:31px;margin-bottom:11px}
.login-now{height:35px;border-radius:3px;background:linear-gradient(#f4ea4a,#e2cf1e);border-bottom:3px solid #c9b415;text-align:center;font-size:16px;font-weight:600;line-height:33px;margin-top:1px}
.login-links{margin-top:9px;font-size:13.5px}
.login-links .or{color:var(--link-blue)}
.hero-mark{position:absolute;left:581px;top:200px;width:38px;height:38px;border-radius:50%;background:var(--orange)}
.headline{position:absolute;left:0;width:1200px;top:262px;text-align:center;font-family:"Raleway",sans-serif;font-weight:800;font-size:26px;color:var(--ink);text-shadow:0 0 6px rgba(255,255,255,.8)}
.feed-panel{position:absolute;left:249px;top:303px;width:696px;height:419px;background:var(--panel);border-radius:3px;box-shadow:0 2px 8px rgba(0,0,0,.4)}
.feed-title,.slogan{position:absolute;left:0;width:100%;text-align:center;font-family:"Raleway",sans-serif;font-weight:800;font-size:26px;color:var(--white)}
.feed-title{top:18px}
.slogan{top:325px}
.chips{position:absolute;left:28px;top:67px;width:638px}
.chip-row{display:flex;justify-content:space-between;height:41px;margin-bottom:9px}
.chip{display:flex;height:41px;border-radius:2px;overflow:hidden;font-size:12.5px;align-items:center}
.chip-icon{width:34px;height:41px;background:var(--white);display:flex;align-items:center;justify-content:center}
.chip-icon span{width:14px;height:14px;border-radius:50%;background:#222}
.chip-label{flex:1;height:41px;line-height:41px;padding-left:9px;white-space:nowrap}
.y{background:var(--yellow)}.p{background:var(--purple)}.o{background:var(--orange)}.k{background:var(--pink)}
.connect{position:absolute;left:181px;top:372px;display:flex;align-items:center;gap:10px;font-family:Arial,sans-serif}
.social-btn{display:flex;width:185px;height:28px;background:var(--social);color:var(--white);font-size:12.5px;font-weight:700;align-items:center;border-radius:2px}
.social-btn .sq{width:30px;height:28px;border-right:1px solid rgba(0,0,0,.25);display:flex;align-items:center;justify-content:center}
.social-btn .sq span{width:10px;height:10px;background:var(--white)}
.social-btn .txt{flex:1;text-align:center}
.default-way{font-size:12px;color:#aaa}
.default-way b{color:#2ea6f0}
.footer{position:absolute;left:0;top:855px;width:1200px;height:54px;background:var(--bar);display:flex;justify-content:center;align-items:center;color:var(--white);font-size:13px;gap:8px}
</style>
</head>
<body>
<div class="hero-bg" role="img" aria-label="Blurred photo of shoppers walking through a city shopping mall"></div>

<header class="topbar">
  <div class="brand"><span>BrinoKet</span><span class="brand-dot"></span></div>
  <div class="search">
    <div class="search-field">Search</div>
    <div class="search-btn"><svg width="16" height="16" viewBox="0 0 16 16"><circle cx="6.5" cy="6.5" r="4.5" fill="none" stroke="#222" stroke-width="2"/><line x1="10" y1="10" x2="14.5" y2="14.5" stroke="#222" stroke-width="2.4"/></svg></div>
  </div>
  <nav class="nav"><span>HOW IT WORKS</span><span>|</span><span>BUSINESS</span></nav>
  <div class="login-toggle">LOGIN</div>
</header>

<form class="login-panel">
  <div class="input">Username</div>
  <div class="input">Password</div>
  <div class="login-now">LOGIN NOW</div>
  <p class="login-links">Forgot Your Password &nbsp;<span class="or">or</span> Signup</p>
</form>

<div class="hero-mark"></div>
<h1 class="headline">SHOP DIRECTLY FROM YOUR PROFILE</h1>

<section class="feed-panel">
  <h2 class="feed-title">SETUP YOUR FEED</h2>
  <div class="chips">
    <div class="chip-row">
      <div class="chip y" style="width:122px"><div class="chip-icon"><span></span></div><div class="chip-label">ACTIVE LIFE</div></div>
      <div class="chip p" style="width:194px"><div class="chip-icon"><span></span></div><div class="chip-label">ARTS &amp; ENTERTAINMENT</div></div>
      <div class="chip o" style="width:129px"><div class="chip-icon"><span></span></div><div class="chip-label">AUTOMOTIVE</div></div>
      <div class="chip k" style="width:170px"><div class="chip-icon"><span></span></div><div class="chip-label">&nbsp;&nbsp;BEAUTY &amp; SPAS</div></div>
    </div>
    <div class="chip-row">
      <div class="chip o" style="width:122px"><div class="chip-icon"><span></span></div><div class="chip-label">EDUCATION</div></div>
      <div class="chip k" style="width:219px"><div class="chip-icon"><span></span></div><div class="chip-label">EVENT PLANNING &amp; SERVICES</div></div>
      <div class="chip y" style="width:167px"><div class="chip-icon"><span></span></div><div class="chip-label">FINANCIAL SERVICES</div></div>
      <div class="chip p" style="width:105px"><div class="chip-icon"><span></span></div><div class="chip-label">HOTELS</div></div>
    </div>
    <div class="chip-row">
      <div class="chip y" style="width:162px"><div class="chip-icon"><span></span></div><div class="chip-label">HEALTH &amp; MEDICAL</div></div>
      <div class="chip p" style="width:153px"><div class="chip-icon"><span></span></div><div class="chip-label">HOME SERVICES</div></div>
      <div class="chip o" style="width:153px"><div class="chip-icon"><span></span></div><div class="chip-label">FOOD &amp; DRINK</div></div>
      <div class="chip k" style="width:142px"><div class="chip-icon"><span></span></div><div class="chip-label">REAL ESTATE</div></div>
    </div>
    <div class="chip-row">
      <div class="chip k" style="width:146px"><div class="chip-icon"><span></span></div><div class="chip-label">LOCAL SERVICES</div></div>
      <div class="chip o" style="width:136px"><div class="chip-icon"><span></span></div><div class="chip-label">MASS MEDIA</div></div>
      <div class="chip y" style="width:113px"><div class="chip-icon"><span></span></div><div class="chip-label">NIGHTLIFE</div></div>
      <div class="chip p" style="width:215px"><div class="chip-icon" style="width:50px"><span></span></div><div class="chip-label">PROFESSIONAL SERVICES</div></div>
    </div>
    <div class="chip-row">
      <div class="chip o" style="width:81px"><div class="chip-icon"><span></span></div><div class="chip-label">PETS</div></div>
      <div class="chip k" style="width:126px"><div class="chip-icon"><span></span></div><div class="chip-label">SHOPPING</div></div>
      <div class="chip y" style="width:147px"><div class="chip-icon"><span></span></div><div class="chip-label">RESTAURANTS</div></div>
      <div class="chip p" style="width:258px"><div class="chip-icon"><span></span></div><div class="chip-label">PUBLIC SERVICES &amp; GOVERNMENT</div></div>
    </div>
  </div>
  <h2 class="slogan">SAVE YOUR TIME LIVE BETTER</h2>
  <div class="connect">
    <div class="social-btn"><div class="sq"><span></span></div><div class="txt">Connect with Friendlink</div></div>
    <span class="default-way">or <b>Sign In</b> by default way</span>
  </div>
</section>

<footer class="footer">
  <span>About us</span><span>|</span><span>Blog</span><span>|</span><span>Business</span><span>|</span><span>Jobs</span><span>|</span><span>Privacy</span><span>|</span><span>Faq’s</span><span>|</span><span>Contact Us</span>
</footer>
</body>
</html>
```